Ridgeline Journeys business card

please see website
www.ridgelinejourneys.comau

info needed on card
Curtis Halvey
Ph
email
Adventure Riding GPS trails

please use my logo and colours off my site

Curtis Halvey
curtis@ridgelinejourneys.com

```html
<!DOCTYPE html>
<html lang="en">
<head>
<meta charset="utf-8">
<title>Ridgeline Journeys business card</title>
<link rel="stylesheet" href="https://fonts.googleapis.com/css2?family=Open+Sans:wght@300;400;800&display=swap">
<style>
  :root {
    --page: #ebe8e3;
    --card: #ffffff;
    --card-shade: #f1f1f1;
    --ink: #2b2b2b;
    --ink-soft: #555555;
    --accent: #f0d818;
    --accent-soft: #d9e04a;
    --icon-bg: #3a3a3a;
  }
  * { box-sizing: border-box; margin: 0; padding: 0; }
  html, body {
    width: 1200px;
    height: 892px;
    overflow: hidden;
    background: var(--page);
    font-family: "Open Sans", Arial, sans-serif;
  }
  .stage {
    position: relative;
    width: 1200px;
    height: 892px;
  }
  .card {
    position: absolute;
    top: 291px;
    width: 540px;
    height: 310px;
    border-radius: 18px;
    overflow: hidden;
    box-shadow: 0 6px 18px rgba(0,0,0,0.12);
  }
  .card-front {
    left: 40px;
    background: radial-gradient(ellipse at 45% 60%, var(--card) 40%, var(--card-shade) 100%);
  }
  .card-back {
    left: 620px;
    background: linear-gradient(60deg, var(--accent-soft) 0%, #eef0b4 38%, var(--card) 75%, #f3f3f3 100%);
  }
  .brand-name {
    font-weight: 800;
    color: var(--ink);
    text-transform: uppercase;
    line-height: 0.95;
    letter-spacing: 0.5px;
  }
  .card-front .brand {
    position: absolute;
    left: 34px;
    top: 36px;
    display: flex;
    align-items: center;
    gap: 14px;
  }
  .brand-dot {
    width: 34px;
    height: 34px;
    border-radius: 50%;
    background: var(--accent);
  }
  .card-front .brand-name { font-size: 30px; }
  .divider {
    position: absolute;
    left: 0;
    top: 168px;
    width: 330px;
    height: 2px;
    background: var(--accent);
  }
  .person-name {
    position: absolute;
    left: 340px;
    top: 140px;
    font-weight: 300;
    font-size: 29px;
    color: var(--ink);
    white-space: nowrap;
  }
  .contact {
    position: absolute;
    left: 22px;
    bottom: 34px;
    list-style: none;
    display: flex;
    flex-direction: column;
    gap: 10px;
  }
  .contact li {
    display: flex;
    align-items: center;
    gap: 12px;
    font-weight: 300;
    font-size: 16px;
    color: var(--ink-soft);
  }
  .contact-icon {
    width: 14px;
    height: 14px;
    flex: none;
  }
  .card-back .brand {
    position: absolute;
    inset: 0;
    display: flex;
    align-items: center;
    justify-content: center;
    gap: 18px;
  }
  .card-back .brand-name { font-size: 46px; }
</style>
</head>
<body>
<main class="stage">

  <section class="card card-front" aria-label="Card front">
    <div class="brand">
      <span class="brand-dot"></span>
      <span class="brand-name">Ridgeline<br>Journeys</span>
    </div>

    <div class="divider"></div>
    <p class="person-name">Curtis Halvey</p>

    <ul class="contact">
      <li>
        <svg class="contact-icon" viewBox="0 0 14 14" aria-hidden="true">
          <rect width="14" height="14" rx="2" fill="var(--icon-bg)"/>
          <rect x="3" y="4" width="8" height="6" fill="none" stroke="#fff" stroke-width="1"/>
          <path d="M3 4 L7 7.5 L11 4" fill="none" stroke="#fff" stroke-width="1"/>
        </svg>
        curtis@ridgelinejourneys.com
      </li>
      <li>
        <svg class="contact-icon" viewBox="0 0 14 14" aria-hidden="true">
          <rect width="14" height="14" rx="2" fill="var(--icon-bg)"/>
          <circle cx="7" cy="7" r="4" fill="none" stroke="#fff" stroke-width="1"/>
          <path d="M3 7 H11 M7 3 C5 5 5 9 7 11 M7 3 C9 5 9 9 7 11" fill="none" stroke="#fff" stroke-width="0.8"/>
        </svg>
        www.ridgelinejourneys.comau
      </li>
    </ul>
  </section>

  <section class="card card-back" aria-label="Card back">
    <div class="brand">
      <span class="brand-name">Ridgeline<br>Journeys</span>
    </div>
  </section>

</main>
</body>
</html>
```